Business Card Design

We need a business card designed for our new company. Prefer a black card with white logo & writing.

Contact Information for Business Card

Ted Galloway, address: 7-4812 Fernhollow Road, Abbotsford, BC, V3K 8R2, Office Phone: 604-712-3390, Cell: 604-947-2164, Email: ted@resinworkshub.ca

Colors

Designer to choose only greyscale colors for use in the design.

```html
<!DOCTYPE html>
<html lang="en">
<head>
<meta charset="utf-8">
<title>Resinworks Hub — Business Card</title>
<link href="https://fonts.googleapis.com/css2?family=Arimo:wght@400;700&family=Barlow+Semi+Condensed:wght@600;700&display=swap" rel="stylesheet">
<style>
  :root {
    --backdrop: #a4a4a4;
    --card-black: #231f20;
    --card-white: #ffffff;
    --accent-grey: #a7a7a7;
    --ink-dark: #3b3b3b;
    --ink-body: #3f3f3f;
    --icon-grey: #9b9b9b;
    --logo-white: #ffffff;
  }
  * { margin: 0; padding: 0; box-sizing: border-box; }
  html, body { width: 1200px; height: 900px; overflow: hidden; }
  body {
    background: var(--backdrop);
    position: relative;
    font-family: "Arimo", Arial, sans-serif;
  }
  .card {
    position: absolute;
    top: 320px;
    width: 424px;
    height: 256px;
    overflow: hidden;
  }
  .card-front { left: 139px; background: var(--card-black); }
  .card-back { left: 664px; background: var(--card-white); }

  .front-bar {
    position: absolute;
    top: 0;
    width: 7px;
    height: 43px;
    background: var(--accent-grey);
  }
  .front-bar.one { left: 38px; }
  .front-bar.two { left: 50px; }

  .brand {
    position: absolute;
    left: 50%;
    transform: translate(-50%, -50%);
    display: flex;
    align-items: center;
    gap: 7px;
    white-space: nowrap;
  }
  .card-front .brand { top: 119px; }
  .brand-dot {
    width: 12px; height: 12px;
    border-radius: 50%;
    background: var(--logo-white);
  }
  .brand-name {
    font-family: "Barlow Semi Condensed", Arial, sans-serif;
    font-weight: 700;
    font-size: 22px;
    letter-spacing: 0.5px;
    text-transform: uppercase;
    color: var(--logo-white);
  }
  .website {
    position: absolute;
    top: 204px;
    left: 0; right: 0;
    text-align: center;
    font-family: "Arimo", Arial, sans-serif;
    font-weight: 700;
    font-size: 9.5px;
    letter-spacing: 2.4px;
    color: #d9d9d9;
  }

  .back-panel {
    position: absolute;
    left: 0; top: 0;
    width: 189px; height: 100%;
    background: var(--card-black);
  }
  .back-strip {
    position: absolute;
    left: 189px; top: 0;
    width: 9px; height: 100%;
    background: var(--accent-grey);
  }
  .back-panel .brand { top: 128px; }
  .back-panel .brand-name { font-size: 17px; }
  .back-panel .brand-dot { width: 10px; height: 10px; }

  .holder-name {
    position: absolute;
    left: 215px; top: 57px;
    font-family: "Barlow Semi Condensed", Arial, sans-serif;
    font-weight: 700;
    font-size: 17px;
    letter-spacing: 1.3px;
    color: var(--ink-dark);
    text-transform: uppercase;
  }
  .contact-row {
    position: absolute;
    left: 215px;
    display: flex;
    align-items: center;
    font-size: 9.6px;
    line-height: 12.8px;
    color: var(--ink-body);
  }
  .contact-row svg { width: 11px; height: 11px; fill: var(--icon-grey); margin-right: 13px; flex: none; }
  .contact-phone { top: 113px; }
  .contact-email { top: 150px; }
  .contact-address { top: 177px; }
</style>
</head>
<body>
  <section class="card card-front">
    <div class="front-bar one"></div>
    <div class="front-bar two"></div>
    <div class="brand">
      <span class="brand-dot"></span>
      <span class="brand-name">Resinworks Hub</span>
    </div>
    <p class="website">www.resinworkshub.shop</p>
  </section>

  <section class="card card-back">
    <div class="back-panel">
      <div class="brand">
        <span class="brand-dot"></span>
        <span class="brand-name">Resinworks Hub</span>
      </div>
    </div>
    <div class="back-strip"></div>

    <h1 class="holder-name">Ted Galloway</h1>

    <div class="contact-row contact-phone">
      <svg viewBox="0 0 24 24" aria-hidden="true"><path d="M6.6 10.8a15.1 15.1 0 0 0 6.6 6.6l2.2-2.2c.3-.3.7-.4 1-.2 1.1.4 2.3.6 3.6.6.6 0 1 .4 1 1V20c0 .6-.4 1-1 1C10.6 21 3 13.4 3 4c0-.6.4-1 1-1h3.5c.6 0 1 .4 1 1 0 1.3.2 2.5.6 3.6.1.3 0 .7-.2 1z"/></svg>
      <div>604-712-3390 (Office)<br>604-947-2164 (Cell)</div>
    </div>

    <div class="contact-row contact-email">
      <svg viewBox="0 0 24 24" aria-hidden="true"><path d="M2 5h20v2l-10 6L2 7z"/><path d="M2 9l10 6 10-6v10H2z"/></svg>
      <div>ted@resinworkshub.ca</div>
    </div>

    <div class="contact-row contact-address">
      <svg viewBox="0 0 24 24" aria-hidden="true"><path d="M12 2a7 7 0 0 0-7 7c0 5.2 7 13 7 13s7-7.8 7-13a7 7 0 0 0-7-7zm0 9.5A2.5 2.5 0 1 1 12 6.5a2.5 2.5 0 0 1 0 5z"/></svg>
      <div>7-4812 Fernhollow Road,<br>Abbotsford, BC, V3K 8R2</div>
    </div>
  </section>
</body>
</html>
```